KRT Engineering Business Card Design

We’re looking for an elegant, clean, and timeless business card design that communicates experience, capability, and reliability.

KRT Engineering was established in 1995 , we are a Government Contracting company providing Professional Services to the Office of Frontier Affairs, Harbor Protection and the Vantage Collective. Our capabilities include: Acquisition & Program Management; Intelligence & Security Operations; Cyber, IT & Network Operations; Lifecycle Logistics & Asset Readiness; C5ISR Systems Engineering & Sustainment.

We want the card to reflect a straightforward, confident approach to business. The design should feel polished and professional without being flashy or overly corporate.

Design Direction
Clean, sophisticated, and uncluttered
Elegant but understated
Strong typography and thoughtful spacing
A timeless aesthetic rather than something overly trendy
Confident and established, with a sense of substance
Easy to read and practical in a real-world business setting

The overall impression should be: “These are experienced professionals who know what they’re doing, do what they say, and can be relied upon.”

We’re open to creative interpretations. The finished card should feel distinctive through its typography, proportions, layout, and attention to detail rather than through excessive graphics or visual effects.

We’re looking for a design that would make a potential client immediately feel that they’re dealing with a capable, trustworthy, and established company.

Company Colors: Navy and Gold/Yellow (but you do not need to use these colors on the card)
Company Name: KRT Engineering Associates, Inc. (known as KRT Engineering)
Website: krtengineering.com
Company Logo: Navy & Gold (other variations attached)

```html
<!DOCTYPE html>
<html lang="en">
<head>
<meta charset="utf-8">
<title>KRT Engineering Business Card</title>
<link rel="stylesheet" href="https://fonts.googleapis.com/css2?family=Poppins:wght@400;500;700;800&display=swap">
<style>
  :root {
    --stage: #2b2b30;
    --card: #232527;
    --white: #ffffff;
    --gold: #f7dc4a;
    --silver: #9a9ca0;
    --ink: #232527;
  }
  * { margin: 0; padding: 0; box-sizing: border-box; }
  html, body { width: 1200px; height: 801px; overflow: hidden; }
  body {
    background: var(--stage);
    font-family: "Poppins", sans-serif;
    position: relative;
  }
  .card {
    position: absolute;
    top: 240px;
    width: 525px;
    height: 300px;
    background: var(--card);
    border-radius: 3px;
    box-shadow: 0 18px 40px rgba(0,0,0,0.45);
  }
  .card--front { left: 50px; }
  .card--back { left: 625px; }

  .front-name {
    position: absolute;
    inset: 0;
    display: flex;
    align-items: center;
    justify-content: center;
    gap: 14px;
    color: var(--silver);
    font-weight: 800;
    font-size: 54px;
    letter-spacing: 1px;
  }
  .front-name .sub { font-size: 22px; font-weight: 800; letter-spacing: 2px; }

  .person {
    position: absolute;
    left: 34px;
    top: 36px;
  }
  .person__name {
    color: var(--white);
    font-weight: 700;
    font-size: 17px;
    letter-spacing: 0.5px;
    line-height: 1.1;
  }
  .person__role {
    color: var(--gold);
    font-weight: 400;
    font-size: 15px;
    line-height: 1.2;
  }

  .brand {
    position: absolute;
    right: 40px;
    top: 32px;
    display: flex;
    align-items: center;
    gap: 10px;
    color: var(--white);
    font-weight: 800;
    font-size: 50px;
    line-height: 1;
  }
  .brand__dot {
    width: 16px; height: 16px;
    border-radius: 50%;
    background: var(--gold);
  }

  .address {
    position: absolute;
    right: 34px;
    top: 132px;
    text-align: right;
    color: var(--white);
    font-size: 12.5px;
    line-height: 1.45;
  }

  .divider {
    position: absolute;
    left: 34px;
    right: 34px;
    top: 196px;
    height: 1px;
    background: var(--gold);
  }

  .contacts {
    position: absolute;
    left: 34px;
    top: 210px;
    list-style: none;
  }
  .contacts li {
    display: flex;
    align-items: center;
    gap: 9px;
    color: var(--white);
    font-size: 12.5px;
    line-height: 1;
    margin-bottom: 7px;
  }
  .contacts svg { width: 17px; height: 17px; flex: none; }
</style>
</head>
<body>
  <section class="card card--front" aria-label="Card front">
    <div class="front-name">KRT <span class="sub">ENGINEERING</span></div>
  </section>

  <section class="card card--back" aria-label="Card back">
    <div class="person">
      <p class="person__name">OWEN MARSH</p>
      <p class="person__role">Manager</p>
    </div>

    <div class="brand"><span class="brand__dot"></span>KRT</div>

    <address class="address" style="font-style:normal">
      418 Alder Row<br>
      Suite 310, Port Halden<br>
      VA 20190
    </address>

    <div class="divider"></div>

    <ul class="contacts">
      <li>
        <svg viewBox="0 0 20 20" aria-hidden="true"><circle cx="10" cy="10" r="10" fill="#f7dc4a"/><path d="M7 5.5l2 2-1.2 1.4a6 6 0 0 0 3.3 3.3L12.5 11l2 2-1.4 1.5C9.5 14.5 5.5 10.5 5.5 6.9z" fill="#232527"/></svg>
        555-214-8830
      </li>
      <li>
        <svg viewBox="0 0 20 20" aria-hidden="true"><circle cx="10" cy="10" r="10" fill="#f7dc4a"/><rect x="5" y="6.5" width="10" height="7" fill="none" stroke="#232527" stroke-width="1.4"/><path d="M5 6.5l5 4 5-4" fill="none" stroke="#232527" stroke-width="1.4"/></svg>
        omarsh@krtengineering.com
      </li>
      <li>
        <svg viewBox="0 0 20 20" aria-hidden="true"><circle cx="10" cy="10" r="10" fill="#f7dc4a"/><circle cx="10" cy="10" r="5" fill="none" stroke="#232527" stroke-width="1.3"/><ellipse cx="10" cy="10" rx="2.2" ry="5" fill="none" stroke="#232527" stroke-width="1.1"/><path d="M5 10h10" stroke="#232527" stroke-width="1.1"/></svg>
        www.krtengineering.com
      </li>
    </ul>
  </section>
</body>
</html>
```